Automotive Business Card Design

I would just like a automotive themed card. nothing too extravagant, but catchy.

needs to say something about doing roadside assistance,mobile repairs, Diesel repairs, and Fleet maintenance

it can be single sided or double sided. no preference there.

Industry/Entity Type

Automotive

Contact Information for Business Card

Dean Marlowe
phone 534 861 2093
Name: Brightpath Automotive & Diesel Repair

```html
<!DOCTYPE html>
<html lang="en">
<head>
<meta charset="utf-8">
<title>Brightpath Automotive &amp; Diesel Repair – Business Card</title>
<link rel="stylesheet" href="https://fonts.googleapis.com/css2?family=Exo+2:ital,wght@0,600;0,700;1,400;1,800&display=swap">
<style>
  :root {
    --backdrop: #ebe8e2;
    --card-white: #fdfdfc;
    --band-pale: #e5e5d0;
    --field-olive: #d8d8b5;
    --ink-green: #1d6a33;
    --shadow: rgba(40, 30, 20, 0.22);
  }
  * { margin: 0; padding: 0; box-sizing: border-box; }
  html, body {
    width: 1200px;
    height: 1037px;
    overflow: hidden;
    background: var(--backdrop);
  }
  .canvas {
    position: relative;
    width: 1200px;
    height: 1037px;
  }
  .business-card {
    position: absolute;
    left: 100px;
    top: 233px;
    width: 1000px;
    height: 571px;
    background: var(--card-white);
    box-shadow: 0 14px 36px var(--shadow);
    overflow: hidden;
  }
  .card-shapes {
    position: absolute;
    inset: 0;
    width: 1000px;
    height: 571px;
  }
  .card-shapes .band { fill: var(--band-pale); }
  .card-shapes .field { fill: var(--field-olive); }
  .company-name {
    position: absolute;
    right: 34px;
    top: 38px;
    font-family: "Exo 2", sans-serif;
    font-weight: 800;
    font-style: italic;
    font-size: 38px;
    letter-spacing: 0.5px;
    text-transform: uppercase;
    color: var(--ink-green);
    white-space: nowrap;
  }
  .contact {
    position: absolute;
    left: 330px;
    top: 168px;
    font-family: "Exo 2", sans-serif;
    color: var(--ink-green);
  }
  .contact-name {
    font-weight: 700;
    font-size: 54px;
    letter-spacing: 7px;
    line-height: 1;
  }
  .contact-phone {
    margin-top: 6px;
    margin-left: 22px;
    font-weight: 600;
    font-size: 34px;
    letter-spacing: 5px;
    line-height: 1;
  }
  .services {
    position: absolute;
    left: 62px;
    top: 330px;
    font-family: "Exo 2", sans-serif;
    color: var(--ink-green);
  }
  .services-title {
    font-weight: 800;
    font-style: italic;
    font-size: 30px;
    line-height: 1.1;
    margin-bottom: 4px;
  }
  .services-list {
    list-style: none;
    font-style: italic;
    font-weight: 400;
    font-size: 26px;
    line-height: 1.22;
  }
</style>
</head>
<body>
<main class="canvas">
  <section class="business-card" aria-label="Business card">
    <svg class="card-shapes" viewBox="0 0 1000 571" aria-hidden="true">
      <rect class="band" x="0" y="0" width="1000" height="30"/>
      <rect class="band" x="0" y="98" width="1000" height="38"/>
      <polygon class="field" points="0,292 790,462 420,571 0,571"/>
      <polygon class="field" points="1000,418 1000,571 530,571"/>
    </svg>

    <h1 class="company-name">Brightpath Automotive &amp; Diesel Repair</h1>

    <div class="contact">
      <p class="contact-name">Dean Marlowe</p>
      <p class="contact-phone">534 861 2093</p>
    </div>

    <div class="services">
      <h2 class="services-title">SERVICES</h2>
      <ul class="services-list">
        <li>Roadside assistance</li>
        <li>Mobile repairs</li>
        <li>Diesel repairs</li>
        <li>And Fleet maintenance</li>
      </ul>
    </div>
  </section>
</main>
</body>
</html>
```